Hardcore nerd needs to stand out in a sea of dull Defence business cards

Wombarra Devices is a new Australian consulting engineering company that turns research and theory into practical systems. No evangelistic fluff, just mathematics and physics into electronic and optical circuits for consumer products, scientific research or Defence applications.

We already have a recognised logo (provided) which is often dark blue/black on a light background but we're open to other combinations. (Us engineers tend to have limited aesthetic imagination :)

Some of our recent products have included:
* Instrumentation for electrical testing,
* Radar jammers,
* GPS antenna design,
* Satellite tracking systems,
* High power lasers

We're open to both single and double-sided designs - happy to be convinced either way.

P.S. Another group is working on the web page, so - alas - our web site is currently of no use for images/ideas...

Target Market(s)

Engineering managers,
Scientists

Contact Information for Business Card

Dr Colin Harte
R&D Engineer

colin@wombarradevices.com.au
0427 563 710

PO Box XXX (to be confirmed)
Kelsby ACT 2917
Australia

Font styles to use
Serif
Sans Serif

Colors

Designer to choose colors to be used in the design.

Requirements
Must have
• My contact details!
• I've had many (great) "bold and plain" designs submitted already, so feel free to be artistically creative :)
• Happy to take advice re fonts/colours/printability etc.
Nice to have
• I'm not sure if "lists" are more at home on a CV than a business card, but representative services include:
• Applied electromagnetics
• RF and high speed electronics
• Signal and image processing
• Electro-optical and laser systems
• Concept-to-prototype design services
• If you're considering double sided cards, then often measuring/alignment grids/rulers feature on the back of similar cards.
• e.g. https://www.veltranoptics.example/newgrouppage9.cfm?objectgroup_id=4183
• https://www.veltranoptics.example/newgrouppage9.cfm?objectgroup_ID=4185
• ..or even a "Smith chart" (google will return lots)
• Generic images to represent a capability might work - googling images associated with keyword for each of these areas might help:
• - "passive radar", "phased array", "fdtd", "vircator"
• RF and high speed electronic design
• - "smith chart", "microstrip circuits", "dimensioned drawing", "electronic schematic"
• - "dft", "iir filter"
• - "optical cavity". "laser energy level diagram"
• Background/watermarked images outlines/wireframes/schematics would probably look OK.
Should not have
• If a list of projects/services is provided, it is important not to make the client feel that this is "all" the company can do. Engineering design is a creative discipline (like graphics :)
• Please, no stock "military" snaps like planes, missiles, etc!

```html
<!DOCTYPE html>
<html lang="en">
<head>
<meta charset="utf-8">
<title>Wombarra Devices – Business Card</title>
<link rel="stylesheet" href="https://fonts.googleapis.com/css2?family=Roboto:ital,wght@0,400;0,500;1,400&family=Roboto+Condensed:ital,wght@1,700&display=swap">
<style>
  :root {
    --bg: #2b2b2d;
    --navy: #0b2466;
    --navy-raised: #12308a;
    --white: #ffffff;
    --ink: #3d3d3f;
    --muted: #5a5a5e;
  }
  * { margin: 0; padding: 0; box-sizing: border-box; }
  html, body { width: 1200px; height: 878px; overflow: hidden; }
  body {
    background: var(--bg);
    font-family: "Roboto", sans-serif;
    position: relative;
  }
  .card {
    position: absolute;
    width: 560px;
    height: 320px;
    border-radius: 22px;
    overflow: hidden;
    box-shadow: 0 10px 30px rgba(0,0,0,.45);
  }
  .card-back { left: 320px; top: 70px; background: var(--navy); }
  .card-front { left: 320px; top: 470px; background: var(--white); }

  .brand {
    position: absolute;
    left: 110px; top: 96px;
    display: flex; align-items: center; gap: 16px;
  }
  .brand-mark {
    width: 58px; height: 58px; border-radius: 50%;
    border: 4px solid var(--navy-raised);
  }
  .brand-name {
    font-family: "Roboto", sans-serif;
    font-weight: 500;
    font-size: 34px;
    letter-spacing: 3px;
    color: var(--navy-raised);
    text-transform: uppercase;
  }
  .services {
    position: absolute;
    left: 110px; top: 196px;
    list-style: none;
    color: var(--white);
    font-size: 16.5px;
    line-height: 1.35;
    letter-spacing: .3px;
  }

  .identity {
    position: absolute;
    right: 300px; top: 104px;
    text-align: right;
  }
  .person-name {
    font-family: "Roboto Condensed", sans-serif;
    font-style: italic;
    font-weight: 700;
    font-size: 38px;
    color: var(--navy);
    letter-spacing: 1px;
    line-height: 1;
    text-transform: uppercase;
  }
  .person-role {
    margin-top: 6px;
    font-style: italic;
    font-size: 17px;
    color: var(--muted);
  }
  .divider {
    position: absolute;
    left: 282px; top: 100px;
    width: 2px; height: 64px;
    background: var(--navy);
  }
  .contacts {
    position: absolute;
    left: 300px; top: 104px;
    list-style: none;
    font-style: italic;
    font-size: 16px;
    color: var(--ink);
    line-height: 1.5;
  }
  .contacts li { display: flex; align-items: center; gap: 8px; }
  .contacts svg { width: 13px; height: 13px; fill: none; stroke: var(--navy); stroke-width: 1.6; }
  .address {
    position: absolute;
    left: 40px; bottom: 30px;
    font-style: italic;
    font-size: 17px;
    color: var(--ink);
    letter-spacing: .4px;
  }
</style>
</head>
<body>
  <section class="card card-back">
    <div class="brand">
      <div class="brand-mark"></div>
      <div class="brand-name">Wombarra Devices</div>
    </div>
    <ul class="services">
      <li>* Instrumentation for electrical testing,</li>
      <li>* Radar jammers, * GPS antenna design,</li>
      <li>* Satellite tracking systems, * High power lasers</li>
    </ul>
  </section>

  <section class="card card-front">
    <div class="identity">
      <div class="person-name">Dr Colin Harte</div>
      <div class="person-role">R&amp;D Engineer</div>
    </div>
    <div class="divider"></div>
    <ul class="contacts">
      <li>
        <svg viewBox="0 0 14 14"><path d="M3 1.5l2 .5.8 3-1.5 1a7 7 0 0 0 3.7 3.7l1-1.5 3 .8.5 2c-1 1.5-3 1.5-5 .3A11 11 0 0 1 2.7 6.5C1.5 4.5 1.5 2.5 3 1.5z"/></svg>
        0427 563 710
      </li>
      <li>
        <svg viewBox="0 0 14 14"><rect x="1" y="3" width="12" height="8.5" rx="1"/><path d="M1.5 3.5L7 8l5.5-4.5"/></svg>
        colin@wombarradevices.com.au
      </li>
      <li>
        <svg viewBox="0 0 14 14"><circle cx="7" cy="7" r="5.8"/><ellipse cx="7" cy="7" rx="2.6" ry="5.8"/><path d="M1.2 7h11.6M2.2 4h9.6M2.2 10h9.6"/></svg>
        www.wombarradevices.com.au
      </li>
    </ul>
    <p class="address">PO Box XXX (to be confirmed) Kelsby ACT 2917 Australia</p>
  </section>
</body>
</html>
```